Business card design for my company.
I would like the card's background colour to be black. You can also see our web site to get an idea of our brand. https://www.tmwhomecrafting.com.au/
- Name
- Email

```html
<!DOCTYPE html>
<html lang="en">
<head>
<meta charset="UTF-8">
<title>TMW Home Crafting — Business Card</title>
<link href="https://fonts.googleapis.com/css2?family=Montserrat:wght@400;500;700;800&display=swap" rel="stylesheet">
<style>
  :root{
    --canvas:#e4e4e2;
    --card:#232323;
    --card-deep:#1a1a1a;
    --chevron:#3a3a3a;
    --green:#1f9a4a;
    --white:#f4f5f5;
    --muted:#d9d9d9;
  }
  *{box-sizing:border-box;margin:0;padding:0}
  html,body{width:1200px;height:912px;overflow:hidden}
  body{
    background:var(--canvas);
    font-family:'Montserrat',sans-serif;
    display:flex;flex-direction:column;align-items:center;justify-content:center;gap:40px;
  }
  .card{
    position:relative;width:700px;height:400px;border-radius:18px;
    background:var(--card);overflow:hidden;
    box-shadow:0 10px 24px rgba(0,0,0,.22);
  }
  .brand{display:flex;align-items:center;gap:16px;color:var(--white)}
  .brand-mark{width:26px;height:26px;background:var(--green);flex:none}
  .brand-name{font-weight:800;letter-spacing:.06em;text-transform:uppercase;line-height:1.1}
  .card-front .brand{position:absolute;left:50%;top:50%;transform:translate(-50%,-50%)}
  .card-front .brand-name{font-size:40px}
  .card-front .brand-mark{width:36px;height:36px}

  .card-back .brand{position:absolute;left:40px;top:178px}
  .card-back .brand-name{font-size:26px}
  .divider{position:absolute;left:400px;top:100px;width:1px;height:190px;background:var(--green)}
  .contact{position:absolute;left:430px;top:92px;color:var(--white)}
  .contact-name{color:var(--green);font-weight:800;font-size:27px;letter-spacing:.02em;text-transform:uppercase}
  .contact-role{font-size:17px;font-weight:400;margin-top:2px}
  .dash{width:18px;height:1px;background:var(--green);margin:18px 0 12px}
  .contact-list{list-style:none;display:flex;flex-direction:column;gap:9px;font-size:14.5px;color:var(--muted)}
  .contact-list li{display:flex;align-items:center;gap:10px}
  .contact-list svg{width:14px;height:14px;flex:none;fill:var(--green)}
  .decor{position:absolute;inset:0;pointer-events:none}
</style>
</head>
<body>
  <section class="card card-front" aria-label="Card front">
    <div class="brand">
      <span class="brand-mark"></span>
      <span class="brand-name">TMW Home Crafting</span>
    </div>
  </section>

  <section class="card card-back" aria-label="Card back">
    <svg class="decor" viewBox="0 0 700 400" preserveAspectRatio="none">
      <polygon points="430,400 560,262 700,262 700,300 590,300 490,400" fill="var(--chevron)"/>
      <polygon points="490,400 590,300 700,300 700,330 520,400" fill="var(--card-deep)"/>
      <polygon points="520,400 700,330 700,400" fill="var(--white)"/>
      <polygon points="0,388 528,352 520,400 0,400" fill="var(--green)"/>
    </svg>

    <div class="brand">
      <span class="brand-mark"></span>
      <span class="brand-name">TMW Home<br>Crafting</span>
    </div>

    <div class="divider"></div>

    <div class="contact">
      <p class="contact-name">Daniel Hart</p>
      <p class="contact-role">CEO/Founder</p>
      <div class="dash"></div>
      <ul class="contact-list">
        <li>
          <svg viewBox="0 0 24 24"><path d="M6.6 10.8a15 15 0 0 0 6.6 6.6l2.2-2.2c.3-.3.7-.4 1-.2 1.1.4 2.3.6 3.6.6.6 0 1 .4 1 1V20c0 .6-.4 1-1 1C10.6 21 3 13.4 3 4c0-.6.4-1 1-1h3.5c.6 0 1 .4 1 1 0 1.3.2 2.5.6 3.6.1.3 0 .7-.2 1z"/></svg>
          555-014-2290
        </li>
        <li>
          <svg viewBox="0 0 24 24"><path d="M2 5h20v14H2z M3 6l9 7 9-7" stroke="var(--card)" stroke-width="1.5"/></svg>
          info@tmwhomecrafting.com.au
        </li>
        <li>
          <svg viewBox="0 0 24 24"><circle cx="12" cy="12" r="10"/><path d="M2 12h20M12 2c3 3 3 17 0 20M12 2c-3 3-3 17 0 20" stroke="var(--card)" stroke-width="1.4" fill="none"/></svg>
          www.tmwhomecrafting.com.au
        </li>
      </ul>
    </div>
  </section>
</body>
</html>
```